Beautiful Upgraded Single Story Home in Avonlea...SOLD in 3 days for top $$!

This is a 6.5" x 11" QPRX postcard. Please use the indicia files and 6.5" x 11" template attached in the brief.

Reason: We are still working on the details for one of the postcards. Thanks

Target Market(s)

Listings

Font styles to use
Serif

Colors
33b8a4

Requirements
Must have
• Call me if you are interested in getting the most amount of equity out of your home!
• Marisol Tandy (949) 555-0142 and Doreen Waltcroft (909) 555-0187
• Marisol@CrewWaltcroft.example and Doreen@CrewWaltcroft.example
• Bright Hollow Properties
• The Key to your Real Estate Needs!
• (At bottom of postcard) "If you are currently listed with a licensed Realtor, this is not intended as solicitation"
Nice to have
• The Front Should be the Property Picture and "In Escrow in 3 Days!"

```html
<!DOCTYPE html>
<html lang="en">
<head>
<meta charset="utf-8">
<title>Sold in 3 Days – Postcard Front and Back</title>
<link href="https://fonts.googleapis.com/css2?family=Roboto+Condensed:ital,wght@0,300;0,400;0,700;0,900;1,700;1,900&display=swap" rel="stylesheet">
<style>
  :root{
    --stage:#1d5d8c;
    --teal:#33b8a4;
    --teal-deep:#3e8f7c;
    --red:#e8262a;
    --ink:#111111;
    --paper:#ffffff;
    --logo-paper:#f3f0ea;
  }
  *{box-sizing:border-box;margin:0;padding:0}
  html,body{width:1200px;height:1200px;overflow:hidden}
  body{background:var(--stage);font-family:"Roboto Condensed",Arial,sans-serif;position:relative}
  .card{position:absolute;overflow:hidden}
  .line{position:absolute;left:0;right:0;text-align:center;white-space:nowrap}

  /* Front */
  .card-front{left:101px;top:174px;width:498px;height:897px;
    background:linear-gradient(180deg,#4f9a86 0%,#6fae9c 40%,#c9ddd6 62%,#e4ece9 75%)}
  .front-escrow{top:28px;font-size:52px;font-weight:300;color:var(--paper)}
  .front-days{top:84px;font-size:90px;font-weight:900;color:var(--paper);letter-spacing:-1px}
  .front-listing{top:176px;font-size:27px;font-weight:400;color:var(--ink);line-height:34px}
  .house-photo{position:absolute;left:0;top:420px;width:498px;height:360px;
    background:linear-gradient(180deg,#dfe9e6 0%,#6f8f94 35%,#5c6f7b 60%,#3f4a50 85%,#2a3338 100%)}
  .front-footer{position:absolute;left:0;bottom:0;width:498px;height:150px}
  .front-contacts{top:812px;font-size:24px;font-weight:700;font-style:italic;color:var(--paper);line-height:29px}

  .sold-band{position:absolute;left:0;width:100%}
  .sold-word{position:absolute;font-weight:900;font-style:italic;color:var(--red);
    text-shadow:3px 3px 0 #fff,-2px -2px 0 #fff,2px -2px 0 #fff,-2px 2px 0 #fff}
  .front-sold{left:132px;top:262px;font-size:108px;transform:rotate(-5deg)}
  .front-tagline{left:70px;top:380px;font-size:38px;font-weight:900;font-style:italic;color:var(--ink);transform:rotate(-6deg);transform-origin:left center;white-space:nowrap;position:absolute}

  .logo-box{position:absolute;background:var(--logo-paper);border:4px solid var(--ink);
    outline:4px solid var(--paper);display:flex;align-items:center;justify-content:center;gap:10px;
    font-size:26px;font-weight:700;color:var(--ink);text-align:center;line-height:1.1}
  .logo-mark{width:18px;height:18px;background:var(--ink);flex:none}
  .front-logo{left:120px;top:678px;width:264px;height:122px}

  /* Back */
  .card-back{left:654px;top:218px;width:479px;height:862px;background:var(--paper)}
  .hand-photo{position:absolute;left:146px;top:86px;width:333px;height:452px;
    background:linear-gradient(120deg,#ffffff 0%,#c9c9c9 25%,#5a5d63 55%,#2f3238 100%)}
  .back-bottom{position:absolute;left:0;top:538px;width:479px;height:324px;background:var(--teal)}
  .back-escrow{top:38px;color:var(--teal);font-size:34px;font-weight:400}
  .back-escrow b{font-size:52px;font-weight:900}
  .back-sold{left:128px;top:80px;font-size:100px;transform:rotate(-8deg)}
  .back-tagline{position:absolute;left:188px;top:188px;font-size:38px;font-weight:900;font-style:italic;
    color:var(--teal);text-shadow:2px 2px 0 #1a1a1a;transform:rotate(-8deg);white-space:nowrap}
  .back-logo{left:114px;top:484px;width:248px;height:114px;font-size:24px}
  .back-call{top:650px;font-size:22px;font-weight:700;color:var(--paper);line-height:26px}
  .back-contacts{top:732px;font-size:23px;font-weight:300;color:var(--paper);line-height:27px}
  .back-disclaimer{top:800px;font-size:12.5px;font-weight:700;color:#1d3a35;line-height:16px}
</style>
</head>
<body>

<section class="card card-front" aria-label="Postcard front">
  <div class="line front-escrow">In Escrow in</div>
  <div class="line front-days">3 DAYS!</div>
  <div class="line front-listing">BEAUTIFUL UPGRADED<br>SINGLE STORY HOME<br>IN AVONLEA</div>

  <div class="house-photo" role="img" aria-label="Photo of the sold two-storey suburban home at dusk with lit garage and wet driveway"></div>
  <svg class="front-footer" viewBox="0 0 498 150" aria-hidden="true">
    <path d="M0 30 Q249 -10 498 20 L498 150 L0 150 Z" fill="#000"/>
  </svg>

  <svg class="sold-band" style="top:310px" width="498" height="120" viewBox="0 0 498 120" aria-hidden="true">
    <polygon points="0,40 112,30 112,42 0,52" fill="var(--red)"/>
    <polygon points="0,58 112,48 112,60 0,70" fill="var(--red)"/>
    <polygon points="393,4 498,-6 498,6 393,16" fill="var(--red)"/>
    <polygon points="393,22 498,12 498,24 393,34" fill="var(--red)"/>
  </svg>
  <div class="sold-word front-sold">SOLD</div>
  <div class="front-tagline">IN 3 DAYS FOR TOP $$!</div>

  <div class="logo-box front-logo"><span class="logo-mark"></span><span>Bright Hollow<br>Properties</span></div>
  <div class="line front-contacts">MARISOL TANDY (949) 555-0142<br>AND DOREEN WALTCROFT (909) 555-0187</div>
</section>

<section class="card card-back" aria-label="Postcard back">
  <div class="hand-photo" role="img" aria-label="Photo of an agent in a dark suit holding a small model house in an open hand"></div>
  <div class="back-bottom"></div>

  <div class="line back-escrow">In Escrow in <b>3 DAYS!</b></div>
  <svg class="sold-band" style="top:100px" width="479" height="120" viewBox="0 0 479 120" aria-hidden="true">
    <polygon points="0,70 110,60 110,74 0,84" fill="var(--red)"/>
    <polygon points="0,90 110,80 110,94 0,104" fill="var(--red)"/>
    <polygon points="378,20 479,10 479,24 378,34" fill="var(--red)"/>
    <polygon points="378,40 479,30 479,44 378,54" fill="var(--red)"/>
  </svg>
  <div class="sold-word back-sold">SOLD</div>
  <div class="back-tagline">FOR TOP $$!</div>

  <div class="logo-box back-logo"><span class="logo-mark"></span><span>Bright Hollow<br>Properties</span></div>
  <div class="line back-call">CALL ME IF YOU ARE INTERESTED IN<br>GETTING THE MOST AMOUNT OF<br>EQUITY OUT OF YOUR HOME!</div>
  <div class="line back-contacts">MARISOL TANDY (949) 555-0142<br>AND DOREEN WALTCROFT (909) 555-0187</div>
  <div class="line back-disclaimer">IF YOU ARE CURRENTLY LISTED WITH A LICENSED REALTOR,<br>THIS IS NOT INTENDED AS SOLICITATION"</div>
</section>

</body>
</html>
```